verdant terraces simple classy business card design

my name is colin barrow and I run a gardening business aimed at high class verdant terraces. the business name is verdant terraces and our logo was designed on pixel harbour .My clientel are anything from residential homes to businesses. I take pride in my work and know that I offer a service like no other in my area.
The business card will be used to represent my business and I want it to be not only rememberable, but simplistic and modern. Eye catching too. Of course I would like it relatable to gardening and appealing to the correct clientel - those being garden enthusiasts, prestigious homes and businesses that are after top of the line gardening services like no other on the market.
I am not a typical lawn mowing business so I don't want a typical card design that represents that. The gardens I work with are generally million dollar properties with owners who are very garden proud looking for upkeep and guidance from me along with sometimes whole new garden designs. I want the business cards to show to my clients that I take pride, as they do, in their garden. And I want them to know from my card that I am a professional, qualified horticulturist offering them a top of the line service for life. I want them to refer my business on. I want them to look at my business card and see class and professionalism in a modern unique bold way.
The card should be simple with the possibility of the logo on the front being embossed/debossed and my details on the back the card should have a organic garden feel it's very important to me that it is absolutely perfect
I am also very open to ideas and suggestions so look forward to seeing the designs. the business logo has been supplied with this project and I want the card to be double sided

Contact info is
Colin Barrow - Managing Director / Horticulturist
Phone : 0481 526 704
Email: colinbarrow@verdantterraces.example.au

Target Market(s)

high class gardens residential and commercial

Industry/Entity Type

Gardener

Contact Information for Business Card

Contact info is
Phone : 0481 526 704

PLEASE MAKE CARD DOUBLE SIDED

Requirements
Must have
• organic simple classy modern feel
• must flow with the current logo that has been supplied with this project
• Double sided
• Must explain in a simple way that I deal with high end gardens and I'm a qualified horticulturist
Nice to have
• embossed debossed logo
Should not have
• shouldn't be to busy or cheap looking

```html
<!DOCTYPE html>
<html lang="en">
<head>
<meta charset="utf-8">
<title>Verdant Terraces – Business Card</title>
<link href="https://fonts.googleapis.com/css2?family=Source+Sans+3:wght@400;600&family=Cinzel:wght@400&display=swap" rel="stylesheet">
<style>
  :root {
    --backdrop-top: #2a2a2a;
    --backdrop-bottom: #050505;
    --card: #ffffff;
    --leaf: #4f9a3f;
    --leaf-soft: #6aa85a;
    --ink: #444444;
  }
  * { margin: 0; padding: 0; box-sizing: border-box; }
  html, body { width: 1200px; height: 900px; overflow: hidden; }
  body {
    position: relative;
    background: linear-gradient(to bottom, var(--backdrop-top), var(--backdrop-bottom));
    font-family: "Source Sans 3", Arial, sans-serif;
  }
  .card {
    position: absolute;
    top: 306px;
    width: 440px;
    height: 271px;
    background: var(--card);
    border-radius: 12px;
  }
  .card--details { left: 149px; }
  .card--brand { left: 608px; }

  .emblem {
    position: absolute;
    border-radius: 50%;
    background: var(--leaf-soft);
  }
  .card--details .emblem { left: 50px; top: 62px; width: 112px; height: 112px; }
  .card--brand .emblem { left: 175px; top: 76px; width: 70px; height: 70px; }

  .details { position: absolute; left: 200px; top: 70px; color: var(--ink); font-size: 12px; line-height: 15px; }
  .details__name { color: var(--leaf); font-size: 15px; font-weight: 600; line-height: 18px; }
  .details__title { margin-bottom: 12px; }
  .details__address { margin-bottom: 12px; }
  .contact-list { list-style: none; }
  .contact-list li { display: flex; align-items: center; height: 16px; font-size: 11.5px; white-space: nowrap; }
  .contact-list svg { width: 9px; height: 9px; margin-right: 7px; fill: var(--leaf); flex: none; }

  .wordmark {
    position: absolute;
    left: 0; right: 0; top: 150px;
    text-align: center;
    color: var(--leaf);
    font-family: "Cinzel", Georgia, serif;
    font-size: 27px;
    font-weight: 400;
    letter-spacing: 3px;
    text-transform: uppercase;
  }
</style>
</head>
<body>
  <section class="card card--details">
    <div class="emblem" role="img" aria-label="Verdant Terraces emblem"></div>
    <div class="details">
      <p class="details__name">Colin Barrow</p>
      <p class="details__title">Managing Director / Horticulturist</p>
      <p class="details__address">12345, Address Goes Here<br>Country Name, 123456.</p>
      <ul class="contact-list">
        <li><svg viewBox="0 0 10 10" aria-hidden="true"><path d="M2 0.5 L3.8 2.6 L3 3.8 C3.7 5.2 4.8 6.3 6.2 7 L7.4 6.2 L9.5 8 L8.5 9.5 C4.5 9.3 0.7 5.5 0.5 1.5 Z"/></svg>0481 526 704</li>
        <li><svg viewBox="0 0 10 10" aria-hidden="true"><path d="M0.5 2 H9.5 V8 H0.5 Z M1 2.5 L5 5.5 L9 2.5" /></svg>colinbarrow@verdantterraces.example.au</li>
        <li><svg viewBox="0 0 10 10" aria-hidden="true"><circle cx="5" cy="5" r="4.5"/></svg>www.verdantterraces.example.au</li>
      </ul>
    </div>
  </section>

  <section class="card card--brand">
    <div class="emblem" role="img" aria-label="Verdant Terraces emblem"></div>
    <p class="wordmark">Verdant Terraces</p>
  </section>
</body>
</html>
```